Business card for medical clinic

I need an upmarket, modern medical/health business card for my clinic

Contact Information for Business Card

name, address, email, qr code

```html
<!DOCTYPE html>
<html lang="en">
<head>
<meta charset="utf-8">
<title>Meridian Care Clinic – Business Card</title>
<link href="https://fonts.googleapis.com/css2?family=Montserrat:wght@400;500;700&display=swap" rel="stylesheet">
<style>
  :root {
    --stage: #3a3a3c;
    --navy: #1d2643;
    --royal: #3a5bc4;
    --sky: #29abe2;
    --brand-blue: #1f6fa8;
    --ink: #1b1b1f;
    --paper: #ffffff;
  }
  * { box-sizing: border-box; margin: 0; padding: 0; }
  html, body {
    width: 1200px; height: 1200px; overflow: hidden;
    background: var(--stage);
    font-family: "Montserrat", sans-serif;
  }
  .canvas { position: relative; width: 1200px; height: 1200px; }
  .card {
    position: absolute; left: 150px; width: 900px; height: 514px;
    border-radius: 30px; overflow: hidden;
  }
  /* Back side */
  .card-back { top: 56px; background: var(--navy); }
  .back-pattern {
    position: absolute; inset: 0;
    background: linear-gradient(120deg, rgba(58,91,196,0.35) 0%, rgba(58,91,196,0.08) 35%, rgba(29,38,67,0) 60%);
  }
  .back-brand {
    position: absolute; left: 50%; top: 50%; transform: translate(-50%, -50%);
    display: flex; align-items: center; gap: 16px;
    color: var(--paper); font-weight: 500; font-size: 28px; letter-spacing: 3px;
    text-transform: uppercase; white-space: nowrap;
  }
  .brand-dot {
    width: 34px; height: 34px; border-radius: 50%;
    border: 3px solid currentColor; flex: none;
  }
  /* Front side */
  .card-front { top: 630px; background: var(--paper); }
  .front-wave { position: absolute; inset: 0; }
  .front-brand {
    position: absolute; left: 90px; top: 70px;
    display: flex; align-items: center; gap: 22px;
    color: var(--brand-blue); font-weight: 500; font-size: 44px; letter-spacing: 4px;
    text-transform: uppercase; white-space: nowrap;
  }
  .front-brand .brand-dot { width: 70px; height: 70px; border-width: 5px; }
  .person {
    position: absolute; right: 445px; top: 206px; text-align: right; white-space: nowrap;
  }
  .person-name {
    color: var(--brand-blue); font-weight: 700; font-size: 38px; line-height: 1.1;
  }
  .person-role {
    color: var(--ink); font-weight: 400; font-size: 20px; margin-top: 4px;
  }
  .divider {
    position: absolute; left: 470px; top: 176px; width: 2px; height: 120px;
    background: var(--sky);
  }
  .contacts {
    position: absolute; left: 495px; top: 172px; list-style: none;
  }
  .contacts li {
    display: flex; align-items: center; gap: 14px;
    color: var(--ink); font-size: 19px; font-weight: 400; height: 42px; white-space: nowrap;
  }
  .contacts svg { width: 20px; height: 20px; flex: none; }
</style>
</head>
<body>
<main class="canvas">

  <section class="card card-back" aria-label="Card back">
    <div class="back-pattern" role="img" aria-label="Repeating embossed brand-mark pattern in navy and royal blue"></div>
    <div class="back-brand"><span class="brand-dot"></span>Meridian Care Clinic</div>
  </section>

  <section class="card card-front" aria-label="Card front">
    <svg class="front-wave" viewBox="0 0 900 514" preserveAspectRatio="none" aria-hidden="true">
      <path d="M900 270 C 840 370, 650 400, 450 440 C 330 465, 230 490, 180 514 L 900 514 Z" fill="var(--sky)"/>
      <path d="M900 300 C 845 395, 670 422, 480 458 C 360 480, 270 500, 230 514 L 900 514 Z" fill="var(--paper)"/>
      <path d="M900 310 C 850 405, 680 432, 492 466 C 372 488, 290 506, 260 514 L 900 514 Z" fill="var(--navy)"/>
    </svg>

    <div class="front-brand"><span class="brand-dot"></span>Meridian Care Clinic</div>

    <div class="person">
      <p class="person-name">Daniel Harlow</p>
      <p class="person-role">Managing Director</p>
    </div>

    <div class="divider"></div>

    <ul class="contacts">
      <li>
        <svg viewBox="0 0 24 24"><path fill="var(--sky)" d="M6.6 10.8a15.1 15.1 0 0 0 6.6 6.6l2.2-2.2a1 1 0 0 1 1-.25 11.4 11.4 0 0 0 3.6.57 1 1 0 0 1 1 1V20a1 1 0 0 1-1 1A17 17 0 0 1 3 4a1 1 0 0 1 1-1h3.5a1 1 0 0 1 1 1c0 1.25.2 2.45.57 3.57a1 1 0 0 1-.25 1z"/></svg>
        555.014.2290
      </li>
      <li>
        <svg viewBox="0 0 24 24"><rect x="2" y="5" width="20" height="14" rx="2" fill="var(--sky)"/><path d="M3 6l9 7 9-7" fill="none" stroke="#fff" stroke-width="1.6"/></svg>
        hello@meridiancare.com
      </li>
      <li>
        <svg viewBox="0 0 24 24"><circle cx="12" cy="12" r="10" fill="var(--sky)"/><path d="M2 12h20M12 2c3 3 3 17 0 20M12 2c-3 3-3 17 0 20" fill="none" stroke="#fff" stroke-width="1.4"/></svg>
        www.meridiancare.com
      </li>
    </ul>
  </section>

</main>
</body>
</html>
```